RW Framewell Inc Business cards

We need business cards using our existing logo but slightly modified. Right now the logo says RW Loadbearing Masonry. We want to keep the RW part of the design, but replace the Structural Concrete portion with "FRAMEWELL". Please see the attached file.
Ideally this would be a blank template so we can add Different Names, titles, and phone numbers later.
On the one side we want only the logo and on the other side the detail. I'm attaching an example for you to see.
Please reach out with any other questions. Our address and other details will be given out once we find a design we like.

Target Market(s)

Construction Industry

```html
<!DOCTYPE html>
<html lang="en">
<head>
<meta charset="utf-8">
<title>RW Framewell Inc – Business Cards</title>
<link href="https://fonts.googleapis.com/css2?family=Roboto:wght@400;700;900&display=swap" rel="stylesheet">
<style>
  :root {
    --stage: #e4e5e7;
    --card: #2a2a2c;
    --accent: #1f86d1;
    --silver: #a8aaad;
    --text-light: #c9cacc;
    --divider: #1f86d1;
  }
  * { margin: 0; padding: 0; box-sizing: border-box; }
  html, body { width: 1200px; height: 1200px; overflow: hidden; }
  body {
    background: var(--stage);
    font-family: "Roboto", Arial, sans-serif;
    position: relative;
  }
  .card {
    position: absolute;
    left: 150px;
    width: 900px;
    height: 514px;
    background: var(--card);
    overflow: hidden;
    box-shadow: 0 10px 28px rgba(0,0,0,0.22);
  }
  .card::after {
    content: "";
    position: absolute;
    left: 0; right: 0; bottom: 0;
    height: 12px;
    background: var(--accent);
  }
  .card--details { top: 70px; }
  .card--logo { top: 616px; }

  /* Brand name lockup */
  .brand { position: absolute; text-align: center; font-weight: 900; }
  .brand__initials { display: block; line-height: 1; letter-spacing: 4px; }
  .brand__name { display: block; font-weight: 900; }

  .card--details .brand {
    left: 70px; top: 170px; width: 360px;
    color: var(--accent);
  }
  .card--details .brand__initials { font-size: 120px; }
  .card--details .brand__name { font-size: 26px; letter-spacing: 11px; margin-top: 6px; }

  .card--logo .brand {
    left: 0; right: 0; top: 135px;
    color: var(--silver);
  }
  .card--logo .brand__initials { font-size: 190px; letter-spacing: 8px; }
  .card--logo .brand__name { font-size: 42px; letter-spacing: 22px; margin-top: 10px; padding-left: 22px; }

  .divider {
    position: absolute;
    left: 470px; top: 120px;
    width: 2px; height: 250px;
    background: var(--divider);
  }
  .contact { position: absolute; left: 500px; top: 120px; color: var(--text-light); }
  .contact__name { font-size: 30px; font-weight: 700; color: var(--accent); line-height: 1.1; }
  .contact__title { font-size: 20px; color: var(--text-light); margin-bottom: 34px; }
  .contact__address { font-size: 18px; line-height: 1.4; margin-bottom: 26px; }
  .contact__line { display: flex; align-items: center; gap: 12px; font-size: 18px; line-height: 1.75; }
  .contact__icon { width: 18px; height: 18px; flex: none; }
</style>
</head>
<body>

<section class="card card--details" aria-label="Business card, contact side">
  <div class="brand">
    <span class="brand__initials">RW</span>
    <span class="brand__name">FRAMEWELL</span>
  </div>
  <div class="divider"></div>
  <div class="contact">
    <p class="contact__name">Daniel Hart</p>
    <p class="contact__title">President</p>
    <p class="contact__address">00000 New York, unit 000<br>Street, CA 00000</p>
    <p class="contact__line">
      <svg class="contact__icon" viewBox="0 0 24 24" aria-hidden="true"><path fill="#1f86d1" d="M6.6 10.8a15.1 15.1 0 0 0 6.6 6.6l2.2-2.2c.3-.3.7-.4 1-.2 1.1.4 2.3.6 3.6.6.6 0 1 .4 1 1V20c0 .6-.4 1-1 1A17 17 0 0 1 3 4c0-.6.4-1 1-1h3.5c.6 0 1 .4 1 1 0 1.3.2 2.5.6 3.6.1.3 0 .7-.2 1z"/></svg>
      +00 000 000 000
    </p>
    <p class="contact__line">
      <svg class="contact__icon" viewBox="0 0 24 24" aria-hidden="true"><rect x="2" y="5" width="20" height="14" rx="2" fill="none" stroke="#1f86d1" stroke-width="2"/><path d="M3 6l9 7 9-7" fill="none" stroke="#1f86d1" stroke-width="2"/></svg>
      info@rwframewell.com
    </p>
    <p class="contact__line">
      <svg class="contact__icon" viewBox="0 0 24 24" aria-hidden="true"><circle cx="12" cy="12" r="9" fill="none" stroke="#1f86d1" stroke-width="2"/><path d="M3 12h18M12 3c3 3 3 15 0 18M12 3c-3 3-3 15 0 18" fill="none" stroke="#1f86d1" stroke-width="1.6"/></svg>
      www.rwframewell.com
    </p>
  </div>
</section>

<section class="card card--logo" aria-label="Business card, logo side">
  <div class="brand">
    <span class="brand__initials">RW</span>
    <span class="brand__name">FRAMEWELL</span>
  </div>
</section>

</body>
</html>
```